Business Card for a Dental Office

The design should communicate integrity, quality and reliability. We also want the card look elegant, simple, but still stand out, different from the traditional-dental-office business card.

Industry/Entity Type

Business

```html
<!DOCTYPE html>
<html lang="en">
<head>
<meta charset="utf-8">
<title>Harlow Dental Studio – Business Card</title>
<link href="https://fonts.googleapis.com/css2?family=Arimo:wght@400;700&display=swap" rel="stylesheet">
<style>
  :root {
    --stage: #2e2e30;
    --ink: #0b0b0b;
    --paper: #ffffff;
    --gold: #c9a623;
    --gold-light: #e8d25a;
    --gold-deep: #9c7b12;
    --text-light: #f2f2f2;
  }
  * { margin: 0; padding: 0; box-sizing: border-box; }
  html, body {
    width: 1200px; height: 950px; overflow: hidden;
    background: var(--stage);
    font-family: "Arimo", Arial, sans-serif;
  }
  .card {
    position: absolute; left: 240px;
    width: 720px; height: 411px;
    overflow: hidden;
  }
  .card-front { top: 44px; background: var(--ink); }
  .card-back { top: 495px; background: var(--paper); }

  /* front */
  .front-brand {
    position: absolute; left: 0; right: 0; top: 150px;
    display: flex; align-items: center; justify-content: center; gap: 16px;
  }
  .brand-square { width: 40px; height: 40px; background: var(--gold); }
  .front-brand .brand-name {
    color: var(--text-light); font-weight: 700; font-size: 30px; letter-spacing: 1px;
  }
  .front-web {
    position: absolute; left: 0; right: 0; top: 268px; text-align: center;
    color: var(--text-light); font-size: 17px; letter-spacing: 4px;
  }

  /* back */
  .back-art { position: absolute; inset: 0; }
  .back-brand {
    position: absolute; left: 48px; top: 128px;
    display: flex; align-items: center; gap: 10px;
  }
  .back-brand .brand-square { width: 34px; height: 34px; }
  .back-brand .brand-name {
    color: var(--ink); font-weight: 700; font-size: 22px; letter-spacing: 0.5px;
  }
  .tagline {
    position: absolute; left: 92px; top: 160px;
    color: var(--gold); font-size: 9.5px; font-weight: 700; letter-spacing: 0.6px;
  }
  .person { position: absolute; left: 150px; top: 190px; }
  .person-name { color: var(--ink); font-size: 24px; }
  .person-role { color: var(--gold); font-size: 16px; margin-top: 2px; }

  .contact-list {
    position: absolute; right: 34px; top: 120px;
    list-style: none; text-align: right;
  }
  .contact-list li {
    display: flex; align-items: center; justify-content: flex-end; gap: 8px;
    color: var(--text-light); font-size: 14.5px; line-height: 22px;
  }
  .contact-icon { width: 13px; height: 13px; flex: none; }

  .address {
    position: absolute; left: 48px; top: 330px;
    color: var(--text-light); font-size: 17px; line-height: 24px;
  }
</style>
</head>
<body>

<section class="card card-front" aria-label="Card front">
  <div class="front-brand">
    <span class="brand-square"></span>
    <span class="brand-name">HARLOW DENTAL STUDIO</span>
  </div>
  <p class="front-web">www.harlowdental.com</p>
</section>

<section class="card card-back" aria-label="Card back">
  <svg class="back-art" viewBox="0 0 720 411" preserveAspectRatio="none" aria-hidden="true">
    <defs>
      <linearGradient id="goldSweep" x1="0" y1="1" x2="1" y2="0">
        <stop offset="0" stop-color="var(--gold-deep)"/>
        <stop offset="0.5" stop-color="var(--gold-light)"/>
        <stop offset="1" stop-color="var(--gold)"/>
      </linearGradient>
    </defs>
    <path d="M0 411 L0 318 C150 300 300 296 400 210 C490 130 560 60 720 30 L720 411 Z" fill="var(--ink)"/>
    <path d="M0 300 C150 285 290 282 385 200 C475 122 560 52 720 20" fill="none" stroke="url(#goldSweep)" stroke-width="12"/>
    <path d="M0 286 C140 274 280 270 372 193 C460 118 550 48 720 12" fill="none" stroke="url(#goldSweep)" stroke-width="3"/>
  </svg>

  <div class="back-brand">
    <span class="brand-square"></span>
    <span class="brand-name">HARLOW DENTAL STUDIO</span>
  </div>
  <p class="tagline">CARING FOR EVERY SMILE WITH TRUST</p>

  <div class="person">
    <p class="person-name">MARCUS HALE</p>
    <p class="person-role">PRESIDENT</p>
  </div>

  <ul class="contact-list">
    <li>555 0142 7731
      <svg class="contact-icon" viewBox="0 0 13 13"><path d="M3 1 L5 1 L6 4 L4.5 5 C5.3 7 6 7.7 8 8.5 L9 7 L12 8 L12 10 C12 11 11 12 10 12 C5 12 1 8 1 3 C1 2 2 1 3 1 Z" fill="var(--gold)"/></svg>
    </li>
    <li>555 0198 2460
      <svg class="contact-icon" viewBox="0 0 13 13"><rect x="3" y="0.5" width="7" height="12" rx="1.2" fill="var(--gold)"/><rect x="4.2" y="2" width="4.6" height="7.5" fill="var(--ink)"/></svg>
    </li>
    <li>555 0163 9024
      <svg class="contact-icon" viewBox="0 0 13 13"><rect x="3" y="1" width="7" height="4" fill="var(--gold)"/><rect x="1" y="5" width="11" height="7" rx="1" fill="var(--gold)"/><rect x="3.5" y="8" width="6" height="1.5" fill="var(--ink)"/></svg>
    </li>
    <li>marcus@harlowdental.com
      <svg class="contact-icon" viewBox="0 0 13 13"><rect x="0.5" y="2.5" width="12" height="8" fill="var(--gold)"/><path d="M0.5 2.5 L6.5 7 L12.5 2.5" fill="none" stroke="var(--ink)" stroke-width="1"/></svg>
    </li>
    <li>www.harlowdental.com
      <svg class="contact-icon" viewBox="0 0 13 13"><circle cx="6.5" cy="6.5" r="6" fill="var(--gold)"/><path d="M0.5 6.5 H12.5 M6.5 0.5 C3.5 4 3.5 9 6.5 12.5 M6.5 0.5 C9.5 4 9.5 9 6.5 12.5" fill="none" stroke="var(--ink)" stroke-width="0.9"/></svg>
    </li>
  </ul>

  <p class="address">2417 Linden Crest Road<br>Maple Hollow, NY 12045</p>
</section>

</body>
</html>
```